Marcus Delbridge Finance

Need a personal website advertising Equipment Finance,Business Finance,Commercial Finance, Construction Finance, Bridging Finance. Similar websites are www.corvalend.com.au / www.tarmivest.com.au / www.qbr7.com.au /wwwhalvecredit.com.au

Target Market(s)

Business People

Industry/Entity Type

Business

Number of Pages Required

3 page

Font styles to use
Serif
Sans Serif

Requirements
Must have
• All i want is a simple corporate looking website advertising Equipment Finance, Commercial Finance, Construction Finance, Business Finance, Bridging Finance,

```html
<!DOCTYPE html>
<html lang="en">
<head>
<meta charset="utf-8">
<title>Marcus Delbridge Finance</title>
<link href="https://fonts.googleapis.com/css2?family=Open+Sans:wght@400&family=Roboto+Condensed:wght@400&family=Arimo:wght@400&display=swap" rel="stylesheet">
<style>
  :root {
    --blue: #1a8ab8;
    --green: #a6c21c;
    --text: #555;
    --grey-rule: #c8c8c8;
    --white: #fff;
  }
  * { margin: 0; padding: 0; box-sizing: border-box; }
  html, body { width: 1092px; height: 1200px; overflow: hidden; background: var(--white); }
  .page { position: relative; width: 1092px; height: 1200px; font-family: "Open Sans", sans-serif; color: var(--text); }
  .top-band { position: absolute; top: 0; left: 0; width: 100%; height: 9px; background: var(--blue); }
  .brand { position: absolute; left: 72px; top: 28px; font-family: "Arimo", sans-serif; }
  .brand-name { font-size: 36px; color: var(--blue); line-height: 1; white-space: nowrap; }
  .brand-sub { font-size: 22px; color: #555; letter-spacing: 13px; margin-top: 4px; line-height: 1; }
  .nav { position: absolute; top: 55px; left: 0; font-family: "Roboto Condensed", sans-serif; font-size: 19px; }
  .nav a { position: absolute; color: #666; text-decoration: none; white-space: nowrap; }
  .nav a.active { color: var(--blue); }
  .hero { position: absolute; top: 110px; left: 0; width: 1092px; height: 521px;
    background: radial-gradient(ellipse at 45% 40%, #dfe3e6 0%, #9aa3a9 35%, #5d6468 70%, #3c3f42 100%); }
  .welcome { position: absolute; top: 676px; left: 0; width: 100%; text-align: center;
    font-family: "Roboto Condensed", sans-serif; font-size: 38px; color: var(--blue); line-height: 1.2; }
  .welcome .lead { color: var(--green); }
  .welcome-rule { position: absolute; top: 726px; left: 485px; width: 123px; height: 4px; background: var(--grey-rule); }
  .intro { position: absolute; top: 752px; left: 110px; width: 872px; text-align: center; font-size: 14.5px; line-height: 23px; color: #666; }
  .service { position: absolute; top: 862px; width: 180px; text-align: center; }
  .service-icon { width: 104px; height: 104px; border: 1px solid var(--green); border-radius: 50%; margin: 0 auto; display: flex; align-items: center; justify-content: center; }
  .service-title { font-family: "Roboto Condensed", sans-serif; font-size: 23px; color: var(--blue); margin-top: 10px; line-height: 1.2; }
  .service-text { font-size: 15px; line-height: 23px; color: #666; margin-top: 1px; }
  .footer { position: absolute; top: 1103px; left: 0; width: 100%; height: 97px; background: var(--blue); color: var(--white); }
  .footer-links { position: absolute; left: 72px; top: 21px; font-size: 17px; }
  .footer-links a { color: var(--white); text-decoration: none; margin-right: 26px; }
  .copyright { position: absolute; left: 72px; top: 53px; font-size: 15px; }
  .social { position: absolute; top: 26px; width: 44px; height: 44px; border-radius: 50%; border: 2px solid var(--white); }
  .social.filled { background: var(--green); border-color: var(--green); }
</style>
</head>
<body>
<div class="page">
  <div class="top-band"></div>
  <div class="brand">
    <div class="brand-name">Marcus Delbridge Finance</div>
  </div>
  <nav class="nav">
    <a class="active" style="left:594px">HOME</a>
    <a style="left:688px">ABOUT</a>
    <a style="left:796px">SERVICES</a>
    <a style="left:926px">CONTACT</a>
  </nav>

  <div class="hero" role="img" aria-label="Businessman touching a glowing financial chart display with bar and line graphs"></div>

  <h1 class="welcome"><span class="lead">WELCOME TO</span> MARCUS DELBRIDGE FINANCE</h1>
  <div class="welcome-rule"></div>
  <p class="intro">Lorem Ipsum is dummy text of the printing and typesetting industry. Lorem Ipsum has been the industry's standard dummy text ever since the 1500s, when an unknown printer took a galley of type it to make a type specimen book. It has survived not only five centuries, but also the leap into electronic typesetting, remaining essentially unchanged.</p>

  <div class="service" style="left:67px">
    <div class="service-icon">
      <svg width="60" height="60" viewBox="0 0 60 60" fill="none" stroke="#a6c21c" stroke-width="4">
        <circle cx="30" cy="30" r="26"/><circle cx="30" cy="30" r="18" stroke-width="3"/>
        <path d="M12 30h36M30 12v36" stroke-width="3"/>
      </svg>
    </div>
    <div class="service-title">Equipment</div>
    <div class="service-text">Lorem Ipsum is dummy text of the printing and typesetting industry.</div>
  </div>
  <div class="service" style="left:261px">
    <div class="service-icon">
      <svg width="62" height="52" viewBox="0 0 62 52" fill="#a6c21c">
        <rect x="2" y="34" width="9" height="18"/><rect x="16" y="26" width="9" height="26"/><rect x="30" y="32" width="9" height="20"/><rect x="44" y="20" width="9" height="32"/>
        <path d="M2 30 L20 16 L34 26 L52 8" fill="none" stroke="#a6c21c" stroke-width="5"/>
        <path d="M44 2 L60 0 L58 16 Z"/>
      </svg>
    </div>
    <div class="service-title">Business</div>
    <div class="service-text">Lorem Ipsum is dummy text of the printing and typesetting industry.</div>
  </div>
  <div class="service" style="left:456px">
    <div class="service-icon">
      <svg width="62" height="40" viewBox="0 0 62 40" fill="#a6c21c">
        <path d="M2 8 L14 4 L30 18 L22 26 Z"/><path d="M60 8 L48 4 L28 12 L40 32 Z"/>
        <rect x="20" y="22" width="6" height="10" rx="3" transform="rotate(-40 23 27)"/>
        <rect x="28" y="26" width="6" height="10" rx="3" transform="rotate(-40 31 31)"/>
      </svg>
    </div>
    <div class="service-title">Commercial</div>
    <div class="service-text">Lorem Ipsum is dummy text of the printing and typesetting industry.</div>
  </div>
  <div class="service" style="left:653px">
    <div class="service-icon">
      <svg width="60" height="56" viewBox="0 0 60 56" fill="#a6c21c">
        <rect x="0" y="20" width="14" height="36"/><rect x="16" y="0" width="20" height="56"/><rect x="38" y="12" width="12" height="44"/><rect x="50" y="26" width="10" height="30"/>
        <g fill="#fff"><rect x="3" y="25" width="3" height="4"/><rect x="8" y="25" width="3" height="4"/><rect x="3" y="34" width="3" height="4"/><rect x="8" y="34" width="3" height="4"/><rect x="20" y="6" width="4" height="5"/><rect x="28" y="6" width="4" height="5"/><rect x="20" y="18" width="4" height="5"/><rect x="28" y="18" width="4" height="5"/><rect x="20" y="30" width="4" height="5"/><rect x="28" y="30" width="4" height="5"/><rect x="41" y="18" width="3" height="4"/><rect x="41" y="28" width="3" height="4"/></g>
      </svg>
    </div>
    <div class="service-title">Construction</div>
    <div class="service-text">Lorem Ipsum is dummy text of the printing and typesetting industry.</div>
  </div>
  <div class="service" style="left:846px">
    <div class="service-icon">
      <svg width="62" height="40" viewBox="0 0 62 40" fill="none" stroke="#a6c21c" stroke-width="3">
        <path d="M18 2v34M44 2v34M0 28h62"/><path d="M2 26 Q18 2 18 2 Q31 22 44 2 Q44 2 60 26"/><path d="M18 32h26" stroke-width="4"/>
      </svg>
    </div>
    <div class="service-title">Bridging</div>
    <div class="service-text">Lorem Ipsum is dummy text of the printing and typesetting industry.</div>
  </div>

  <footer class="footer">
    <div class="footer-links"><a>Home</a><a>About</a><a>Services</a><a>Contact</a></div>
    <div class="copyright">© Marcus Delbridge - 2017. All Rights Reserved.</div>
    <span class="social filled" style="left:874px"></span>
    <span class="social" style="left:926px"></span>
    <span class="social" style="left:979px"></span>
  </footer>
</div>
</body>
</html>
```